business card for a massage therapy practice named 'Cedar and Willow Massage Studio'

I really need a trendy, yet easy on the eyes business card to complement my logo. Ideally with some gold or rose gold foil work.

My uploaded file of the logo I have in horizontal but I have a vertical version as well. Another color that is used in the website is a blush pink here and there. I'd like to see some trendy tropical leaves in the design.

```html
<!DOCTYPE html>
<html lang="en">
<head>
<meta charset="utf-8">
<title>Cedar and Willow Massage Studio – Business Card</title>
<link href="https://fonts.googleapis.com/css2?family=Open+Sans:wght@400;600&family=Yellowtail&display=swap" rel="stylesheet">
<style>
  :root {
    --backdrop: #6e6e6e;
    --card-white: #fbfcfa;
    --leaf-pale: #e3eee3;
    --leaf-mist: #cfe3d6;
    --leaf-green: #8cc48a;
    --leaf-deep: #3f9a73;
    --copper-light: #eab08c;
    --copper: #d9906a;
    --copper-deep: #b86d4a;
    --ink: #1d1d1d;
    --ink-soft: #333333;
    --accent-diamond: #ec8a5a;
    --frame-line: #9a9a9a;
  }
  * { box-sizing: border-box; margin: 0; padding: 0; }
  html, body { width: 1200px; height: 1200px; overflow: hidden; }
  body {
    background: var(--backdrop);
    font-family: "Open Sans", Arial, sans-serif;
    position: relative;
  }
  .card {
    position: absolute;
    left: 220px;
    width: 760px;
    height: 434px;
    background: var(--card-white);
    overflow: hidden;
    box-shadow: 0 10px 30px rgba(0,0,0,0.35);
  }
  .card--contact { top: 130px; }
  .card--brand { top: 636px; }

  /* Contact side */
  .foliage-wash {
    position: absolute; inset: 0;
    background:
      radial-gradient(ellipse at 20% 20%, var(--leaf-mist) 0%, transparent 55%),
      radial-gradient(ellipse at 85% 70%, var(--leaf-mist) 0%, transparent 50%),
      linear-gradient(135deg, var(--leaf-pale), var(--card-white) 60%, var(--leaf-pale));
  }
  .copper-band { position: absolute; inset: 0; width: 100%; height: 100%; }
  .contact-block {
    position: absolute;
    top: 62px; right: 70px;
    width: 380px;
    text-align: center;
    color: var(--ink);
  }
  .contact-name { font-size: 34px; font-weight: 600; letter-spacing: 1px; }
  .contact-role { font-size: 17px; margin-top: 2px; }
  .contact-line { font-size: 18px; line-height: 1.35; }
  .diamond {
    display: block;
    width: 8px; height: 8px;
    margin: 7px auto;
    background: var(--accent-diamond);
    transform: rotate(45deg);
  }
  .studio-tagline {
    position: absolute;
    left: 44px; top: 196px;
    font-family: "Yellowtail", cursive;
    font-size: 36px;
    line-height: 1.2;
    white-space: nowrap;
    color: var(--ink);
    transform: rotate(16deg);
    transform-origin: left top;
  }

  /* Brand side */
  .foliage-frame {
    position: absolute; inset: 0;
    background:
      radial-gradient(ellipse at 10% 90%, var(--leaf-deep) 0%, transparent 45%),
      radial-gradient(ellipse at 90% 85%, var(--leaf-deep) 0%, transparent 40%),
      radial-gradient(ellipse at 50% 0%, var(--leaf-green) 0%, transparent 55%),
      linear-gradient(160deg, var(--leaf-green), var(--leaf-pale) 50%, var(--leaf-green));
  }
  .brand-panel {
    position: absolute;
    left: 70px; top: 60px; right: 70px; bottom: 60px;
    background: rgba(251,252,250,0.88);
    border: 1.5px solid var(--frame-line);
    display: flex;
    align-items: center;
    justify-content: center;
    gap: 22px;
  }
  .brand-dot {
    width: 34px; height: 34px;
    border-radius: 50%;
    background: var(--copper);
  }
  .brand-name {
    font-family: "Open Sans", Arial, sans-serif;
    font-weight: 600;
    font-size: 44px;
    color: var(--ink);
    letter-spacing: 1px;
  }
</style>
</head>
<body>

<section class="card card--contact">
  <div class="foliage-wash" role="img" aria-label="Soft pale watercolour tropical leaves"></div>
  <svg class="copper-band" viewBox="0 0 760 434" preserveAspectRatio="none" aria-hidden="true">
    <defs>
      <linearGradient id="copperFoil" x1="0" y1="0" x2="1" y2="1">
        <stop offset="0" stop-color="#eab08c"/>
        <stop offset="0.5" stop-color="#d9906a"/>
        <stop offset="1" stop-color="#eab08c"/>
      </linearGradient>
    </defs>
    <path d="M0,140 C200,150 420,300 760,390 L760,434 L0,434 Z" fill="url(#copperFoil)"/>
    <path d="M0,140 C200,150 420,300 760,390" fill="none" stroke="#b86d4a" stroke-width="4"/>
  </svg>
  <div class="contact-block">
    <div class="contact-name">Alex Marlow</div>
    <div class="contact-role">Director | 1-555-010-2040</div>
    <span class="diamond"></span>
    <div class="contact-line">www.cedarandwillow.com</div>
    <div class="contact-line">alex@cedarandwillow.com</div>
    <span class="diamond"></span>
    <div class="contact-line">Harbor City, Northland</div>
  </div>
  <div class="studio-tagline">Cedar and Willow Massage Studio</div>
</section>

<section class="card card--brand">
  <div class="foliage-frame" role="img" aria-label="Watercolour tropical palm and monstera leaves framing the card"></div>
  <div class="brand-panel">
    <span class="brand-dot"></span>
    <span class="brand-name">Cedar &amp; Willow</span>
  </div>
</section>

</body>
</html>
```